Home page design for Drone video business (the Business focusses on home videos for realtors)

Dear reader,

*I NEED DESIGNS OF ALL THE PAGES*
We need a first design of a homepage and of 4 other pages of the website of a business that sells drone video services. All the pages will need to be in the similar design style.
The video's are targeted at consumers that want to sell there home and would like to have a cool drone video of photos of their home.

How does the website look:
- has a navbar on top
- A cool looking banner of an areal drone.
- A Big header: with company name: SkyLoftReels
- A smaller subheader: We film your home to increase your chances of sale
- Then a section with a Big header: How does it work
- In this section a place for a vimeo explainitory video
- Then a similar navbar styled bar with a phone number and a email address
- Then a section where the videos porfolio is displayed in a cool way
- Inside this sectiona header: Our work

- A section with header: Why us?
- 4 symbols here with a subheader and some lorum ipsum text underneath (see wireframe images)

- Under that a: Contact us
- where you can put in name, email, phone, message box and a send button

- At the bottom a footer with phone number and a fake address for now.

Be creative. Use creative but serious color.
Use a serious font. Make it a sharp design. Sharp lines. Not to dark design and not to light design.

The wireframes are the same kind of images.
PLEASE PUT IN DESIGNS OF ALL THE PAGES

Good luck

Target Market(s)

People that want to sell home and want to make a cool drone video or photos of their home.

Industry/Entity Type

Business

Contact Information for Business Card

Lucas Wenning
lucas@skyloftreels.example
+31647208351

Logo Text

SkyLoftReels

Number of Pages Required

1 page

Font styles to use
Sans Serif

Requirements
Must have
• All the sections as explained in the instructions.
• The nav bar should have an about us, services, portfolio and a contact us buttons.
• See instruction for details.
• Must include designs of the front page, contact us, our services, portfolio and contact us.
• If you do add some designs for the "about us", "services", "prices", "portfolio" and "contact us" pages, you make a way better chance of winning the competition.
Nice to have
• designs for the other pages as described at the Must haves. You make a better chance of winning if you include them. Look at the wireframes to see the mockups for those pages. think creative about what kind of sections and design should be included in those pages.
Should not have
• bad designs.

```html
<!DOCTYPE html>
<html lang="en">
<head>
<meta charset="utf-8">
<title>SkyLoftReels – Drone Videos for Home Sellers</title>
<link rel="stylesheet" href="https://fonts.googleapis.com/css2?family=Oswald:wght@400;500&family=Roboto:wght@400;500&display=swap">
<style>
:root{
  --blue:#2a9bd1;
  --blue-dark:#2596cf;
  --blue-light:#4db9e7;
  --why-bg:#3a9dd3;
  --page-grey:#eeeeee;
  --ink:#222222;
  --white:#ffffff;
  --footer:#1b1b1b;
  --field-line:#c9c9c9;
}
*{margin:0;padding:0;box-sizing:border-box}
html,body{width:1200px;height:2795px;overflow:hidden;background:var(--white)}
body{position:relative;font-family:"Roboto",Arial,sans-serif;color:var(--ink)}
.abs{position:absolute}
.display{font-family:"Oswald","Arial Narrow",sans-serif;font-weight:400}

/* header */
.site-header{left:0;top:0;width:1200px;height:99px;background:var(--white)}
.brand{left:86px;top:28px;display:flex;align-items:center;gap:12px}
.brand-dot{width:44px;height:44px;border:3px solid var(--blue);border-radius:50%}
.brand-name{font-family:"Oswald",sans-serif;font-size:29px;color:var(--ink);letter-spacing:.3px}
.main-nav a{position:absolute;top:41px;font-size:16px;color:var(--ink);text-decoration:none;text-transform:uppercase}
.main-nav a.active{color:var(--blue)}

/* hero */
.hero{left:0;top:99px;width:1200px;height:557px;background:linear-gradient(180deg,#6f6a72 0%,#4a4a55 30%,#2b2f3a 60%,#1c2029 100%)}
.hero-title{left:0;width:1200px;top:212px;text-align:center;font-size:50px;color:var(--white);text-transform:uppercase;letter-spacing:-.5px}
.hero-sub{left:0;width:1200px;top:278px;text-align:center;font-size:38px;line-height:41px;color:var(--white)}
.hero-dots{left:555px;top:500px;display:flex;gap:7px}
.hero-dots span{width:11px;height:11px;border-radius:50%;background:var(--white)}
.hero-dots span.on{background:var(--blue)}

/* sections */
.section-title{left:0;width:1200px;text-align:center;font-size:38px;color:var(--blue);text-transform:uppercase}
.how{left:0;top:656px;width:1200px;height:574px;background:var(--page-grey)}
.video{left:194px;top:758px;width:814px;height:421px;background:linear-gradient(180deg,#a9b6be 0%,#7b9a72 30%,#4f7f3e 65%,#5d7a55 100%)}
.video-actions{right:22px;top:34px;display:flex;flex-direction:column;gap:6px}
.video-actions div{width:56px;height:46px;background:rgba(30,30,30,.78);color:var(--white);font-size:10px;font-weight:500;text-align:center;padding-top:6px;border-radius:3px}
.video-actions svg{display:block;margin:0 auto 3px}
.video-bar{left:62px;bottom:20px;width:690px;height:42px;display:flex;align-items:center;gap:12px}
.play-btn{width:90px;height:42px;background:rgba(25,25,25,.85);border-radius:3px;display:flex;align-items:center;justify-content:center}
.progress{flex:1;height:42px;background:rgba(25,25,25,.85);border-radius:3px;position:relative}
.progress .track{position:absolute;left:14px;right:130px;top:20px;height:5px;background:#888}
.progress .fill{position:absolute;left:14px;width:280px;top:20px;height:5px;background:var(--blue)}
.progress .time{position:absolute;left:260px;top:-14px;background:var(--white);color:var(--ink);font-size:12px;padding:1px 6px;border-radius:2px}
.progress .hd{position:absolute;right:40px;top:13px;color:var(--blue);font-size:13px;font-weight:500;font-style:normal}
.progress .vol{position:absolute;right:70px;top:15px;width:40px;height:11px;background:repeating-linear-gradient(90deg,var(--blue) 0 3px,transparent 3px 6px)}

.contact-band{left:0;top:1230px;width:1200px;height:85px;display:flex}
.contact-band div{display:flex;align-items:center;justify-content:center;gap:16px;color:var(--white);font-size:34px}
.band-phone{width:598px;background:var(--blue-dark)}
.band-mail{width:602px;background:var(--blue-light)}

.work{left:0;top:1315px;width:1200px;height:436px;background:var(--white)}
.work-tile{top:1449px;width:246px;height:246px}
.work-tile::after{content:"";position:absolute;inset:8px;border:2px solid rgba(255,255,255,.8)}
.tile-play{position:absolute;left:90px;top:102px;width:66px;height:40px;background:rgba(20,20,20,.8);border-radius:3px;display:flex;align-items:center;justify-content:center;z-index:1}

.why{left:0;top:1751px;width:1200px;height:460px;background:linear-gradient(180deg,#4aa7da 0%,var(--why-bg) 50%,#2e8fc6 100%)}
.why .section-title{color:var(--white)}
.feature-icon{width:75px;height:69px;background:var(--white);border-radius:3px;display:flex;align-items:center;justify-content:center}
.feature-title{font-family:"Oswald",sans-serif;font-size:22px;color:var(--white);text-transform:uppercase}
.feature-text{width:350px;font-size:12.5px;line-height:20px;color:var(--white);text-align:justify}
.feature-more{font-size:11.5px;color:var(--white)}

.contact{left:0;top:2211px;width:1200px;height:481px;background:var(--page-grey)}
.field{background:var(--white);border:1px solid var(--field-line);font-size:12px;color:#555;padding:0 16px;display:flex;align-items:center}
.field.message{align-items:flex-start;padding-top:16px}
.send-btn{left:453px;top:2552px;width:294px;height:66px;background:var(--blue);color:var(--white);font-size:22px;font-weight:500;display:flex;align-items:center;justify-content:center;border-radius:2px}

.site-footer{left:0;top:2692px;width:1200px;height:103px;background:var(--footer);color:var(--white)}
.footer-phone{left:88px;top:24px;font-size:18px;font-weight:500;display:flex;align-items:center;gap:8px}
.footer-address{left:88px;top:56px;font-size:11px}
.footer-copy{left:0;width:1200px;top:46px;text-align:center;font-size:11px}
.footer-brand{left:900px;top:28px;display:flex;align-items:center;gap:10px}
.footer-brand .brand-dot{width:34px;height:34px;border-color:var(--white);border-width:2px}
.footer-brand .brand-name{color:var(--white);font-size:22px}
</style>
</head>
<body>

<header class="site-header abs">
  <div class="brand abs"><span class="brand-dot"></span><span class="brand-name">SkyLoftReels</span></div>
  <nav class="main-nav">
    <a class="active" style="left:533px">Home</a>
    <a style="left:633px">Services</a>
    <a style="left:760px">About us</a>
    <a style="left:890px">Portfolio</a>
    <a style="left:1028px">Contacts</a>
  </nav>
</header>

<section class="hero abs" role="img" aria-label="Aerial photo of a city skyline at dusk with camera drones flying above the towers">
  <h1 class="hero-title abs display">SkyLoftReels</h1>
  <p class="hero-sub abs">We film your home to increase<br>your chances of sale</p>
  <div class="hero-dots abs"><span class="on"></span><span></span><span></span><span></span><span></span></div>
</section>

<section class="how abs">
  <h2 class="section-title abs display" style="top:30px">How does it work?</h2>
</section>
<div class="video abs" role="img" aria-label="Explainer video still: aerial view of a green city park with a monument">
  <div class="video-actions abs">
    <div><svg width="18" height="16" viewBox="0 0 24 22"><path d="M12 21 2 11a5.5 5.5 0 0 1 10-7 5.5 5.5 0 0 1 10 7z" fill="#fff"/></svg>LIKE</div>
    <div><svg width="18" height="16" viewBox="0 0 24 22"><circle cx="5" cy="11" r="3" fill="#fff"/><circle cx="19" cy="4" r="3" fill="#fff"/><circle cx="19" cy="18" r="3" fill="#fff"/><path d="M5 11 19 4M5 11l14 7" stroke="#fff" stroke-width="2"/></svg>SHARE</div>
    <div><svg width="20" height="16" viewBox="0 0 24 18"><path d="M7 3 1 9l6 6M17 3l6 6-6 6M14 1l-4 16" stroke="#fff" stroke-width="2.4" fill="none"/></svg>EMBED</div>
  </div>
  <div class="video-bar abs">
    <div class="play-btn"><svg width="18" height="20" viewBox="0 0 18 20"><path d="M2 1l15 9-15 9z" fill="#fff"/></svg></div>
    <div class="progress"><span class="track"></span><span class="fill"></span><span class="time">00:34</span><span class="vol"></span><span class="hd">HD</span>
      <svg class="abs" style="right:14px;top:14px" width="14" height="14" viewBox="0 0 14 14"><path d="M1 5V1h4M9 1h4v4M13 9v4H9M5 13H1V9" stroke="#fff" stroke-width="2" fill="none"/></svg>
    </div>
  </div>
</div>

<div class="contact-band abs">
  <div class="band-phone"><svg width="30" height="30" viewBox="0 0 30 30"><rect width="30" height="30" rx="5" fill="#fff"/><path d="M9 7c2 0 3 4 3 5s-2 1-1 3 3 4 4 4 1-2 3-1 4 1 4 3-2 3-4 3C13 24 6 17 6 10c0-2 1-3 3-3z" fill="var(--blue-dark)"/></svg>+31647208351</div>
  <div class="band-mail"><svg width="34" height="24" viewBox="0 0 34 24"><rect width="34" height="24" rx="2" fill="#fff"/><path d="M2 3l15 11L32 3" stroke="var(--blue-light)" stroke-width="2.5" fill="none"/></svg>contact@skyloftreels.example</div>
</div>

<section class="work abs">
  <h2 class="section-title abs display" style="top:49px">Our work</h2>
</section>
<div class="work-tile abs" style="left:89px;background:linear-gradient(180deg,#4f8fd0,#b58a5e 60%,#6c6b60)" role="img" aria-label="Portfolio video: wide-angle aerial of a town seen beneath a drone"><span class="tile-play"><svg width="14" height="16" viewBox="0 0 14 16"><path d="M1 1l12 7-12 7z" fill="#fff"/></svg></span></div>
<div class="work-tile abs" style="left:348px;background:linear-gradient(180deg,#9fbfd9,#8d8a6e 40%,#6f7d4f)" role="img" aria-label="Portfolio video: aerial view over a suburban neighbourhood"><span class="tile-play"><svg width="14" height="16" viewBox="0 0 14 16"><path d="M1 1l12 7-12 7z" fill="#fff"/></svg></span></div>
<div class="work-tile abs" style="left:607px;background:linear-gradient(180deg,#4fa2e0,#8cc6ea 45%,#3f7fb0 70%,#6f8f45)" role="img" aria-label="Portfolio video: drone hovering over a lake and autumn forest"><span class="tile-play"><svg width="14" height="16" viewBox="0 0 14 16"><path d="M1 1l12 7-12 7z" fill="#fff"/></svg></span></div>
<div class="work-tile abs" style="left:866px;background:linear-gradient(180deg,#4f7f3a,#6d8e4c 50%,#8a8f6a)" role="img" aria-label="Portfolio video: aerial view of a detached house with garden"><span class="tile-play"><svg width="14" height="16" viewBox="0 0 14 16"><path d="M1 1l12 7-12 7z" fill="#fff"/></svg></span></div>

<section class="why abs" role="img" aria-label="Faint background photo of a drone in flight over blue sky">
  <h2 class="section-title abs display" style="top:40px">Why us?</h2>

  <div class="feature-icon abs" style="left:108px;top:136px"><svg width="32" height="28" viewBox="0 0 32 28"><g fill="none" stroke="var(--blue)" stroke-width="2.5"><ellipse cx="10" cy="19" rx="8" ry="5"/><ellipse cx="22" cy="19" rx="8" ry="5"/><ellipse cx="16" cy="9" rx="8" ry="5"/></g></svg></div>
  <h3 class="feature-title abs" style="left:192px;top:134px">Cheap</h3>
  <p class="feature-text abs" style="left:192px;top:170px">Lorem Ipsum has been the industry's standard dummy text ever since the 1500s, when an unknown printer took a galley of type and scrambled it to make</p>
  <span class="feature-more abs" style="left:194px;top:236px">Read More »</span>

  <div class="feature-icon abs" style="left:650px;top:136px"><svg width="30" height="30" viewBox="0 0 30 30"><circle cx="15" cy="15" r="12" fill="none" stroke="var(--blue)" stroke-width="3"/><circle cx="15" cy="15" r="5" fill="none" stroke="var(--blue)" stroke-width="3"/><path d="M6 6l5 5M24 6l-5 5M6 24l5-5M24 24l-5-5" stroke="var(--blue)" stroke-width="3"/></svg></div>
  <h3 class="feature-title abs" style="left:738px;top:134px">Flexible</h3>
  <p class="feature-text abs" style="left:740px;top:164px">Lorem Ipsum has been the industry's standard dummy text ever since the 1500s, when an unknown printer took a galley of type and scrambled it to make</p>
  <span class="feature-more abs" style="left:742px;top:230px">Read More »</span>

  <div class="feature-icon abs" style="left:108px;top:280px"><svg width="30" height="26" viewBox="0 0 30 26"><rect x="2" y="2" width="26" height="17" fill="none" stroke="var(--blue)" stroke-width="3"/><path d="M10 24h10M15 19v5" stroke="var(--blue)" stroke-width="3"/></svg></div>
  <h3 class="feature-title abs" style="left:192px;top:278px">9K Quality</h3>
  <p class="feature-text abs" style="left:192px;top:312px">Lorem Ipsum has been the industry's standard dummy text ever since the 1500s, when an unknown printer took a galley of type and scrambled it to make</p>
  <span class="feature-more abs" style="left:194px;top:378px">Read More »</span>

  <div class="feature-icon abs" style="left:650px;top:280px"><svg width="30" height="28" viewBox="0 0 30 28"><path d="M2 13 28 2 22 26l-7-8z" fill="var(--blue)"/><path d="M15 18l-3 8v-9" fill="#1f7fb0"/></svg></div>
  <h3 class="feature-title abs" style="left:736px;top:276px">Increase sale chance</h3>
  <p class="feature-text abs" style="left:736px;top:310px">Lorem Ipsum has been the industry's standard dummy text ever since the 1500s, when an unknown printer took a galley of type and scrambled it to make</p>
  <span class="feature-more abs" style="left:736px;top:376px">Read More »</span>
</section>

<section class="contact abs">
  <h2 class="section-title abs display" style="top:50px">Contact us</h2>
</section>
<div class="field abs" style="left:199px;top:2340px;width:252px;height:52px">Name</div>
<div class="field abs" style="left:473px;top:2340px;width:252px;height:52px">Email id</div>
<div class="field abs" style="left:747px;top:2340px;width:252px;height:52px">Phone</div>
<div class="field message abs" style="left:199px;top:2405px;width:802px;height:124px">Message</div>
<div class="send-btn abs">SEND</div>

<footer class="site-footer abs">
  <div class="footer-phone abs"><svg width="16" height="16" viewBox="0 0 30 30"><rect width="30" height="30" rx="5" fill="#fff"/><path d="M9 7c2 0 3 4 3 5s-2 1-1 3 3 4 4 4 1-2 3-1 4 1 4 3-2 3-4 3C13 24 6 17 6 10c0-2 1-3 3-3z" fill="var(--footer)"/></svg>+31647208351</div>
  <p class="footer-address abs">Address : 1420 Harbor View Rd, Fairhaven, NJ</p>
  <p class="footer-copy abs">Copyright © 2016 &nbsp;All Rights</p>
  <div class="footer-brand abs"><span class="brand-dot"></span><span class="brand-name">SkyLoftReels</span></div>
</footer>

</body>
</html>
```